Brightway Haus Inc. Business Card Design

Brightway Haus Inc. is in search of a great clean design for our business cards!

Looking to incorporate our full logo and watermark on side one (however, I am open to having the text and watermark separated within the design.)

On side two, I am looking to have contact information (Name, Position, Phone #, Email, Website (www.thebrightwayhaus.ca). Can have the logo and/or watermark as part of the design if applicable.

Please add tagline "Where Shine Counts" on either side 1 or 2. This tagline can be in a sans serif, serif or cursive font as long as it compliments overall design. Capitalization can be title or sentence case depending on how it fits within the design.

Get creative!! Looking for a clean, crisp, premium design! Looking for a glossy card finish with spot UV features when printed. Cards will also be printed with rounded corners. Standard dimensions (3.5 x 2).

Target Market(s)

B2B - primary clients are business owners or property management corporations. (residential jobs are few and far between)

Industry/Entity Type

Business

Contact Information for Business Card

- clean, crisp design
- double sided
- spot UV accents and glossy finish upon printing
- standard business card size (3.5 x 2) with rounded corners
- please see project description for requirements per side

Font styles to use
Sans Serif

Requirements
Must have
• - adequate bleeds with print ready files
• - cohesive design elements between side 1 & 2
• - spot UV elements (can be on both sides or just one, use your discretion)
• - colour pallet should match the logo file provided
• - incorporate tagline "where shine counts" (this tagline can be in a serif or sans serif font as long as it is complimentary to the overall design.
Nice to have
• - Premium elements with a clean design
Should not have
• - Please omit cartoon or whimsical like designs, think premium.
• - Colours should not stray from the pallet of the provided logo.

```html
<!DOCTYPE html>
<html lang="en">
<head>
<meta charset="utf-8">
<title>Brightway Haus Inc. Business Card</title>
<link rel="stylesheet" href="https://fonts.googleapis.com/css2?family=Open+Sans:wght@400;700&family=Roboto:ital,wght@0,400;1,400&family=Roboto+Condensed:wght@500;700&display=swap">
<style>
  :root {
    --backdrop: #2b2b2b;
    --paper: #f2f2f2;
    --navy: #1b244d;
    --teal: #10aeb2;
    --grey-text: #4a4a4a;
    --rule: #8a8a8a;
    --white: #ffffff;
  }
  * { margin: 0; padding: 0; box-sizing: border-box; }
  html, body { width: 1200px; height: 960px; overflow: hidden; }
  body { background: var(--backdrop); position: relative; font-family: "Roboto", Arial, sans-serif; }

  .card {
    position: absolute;
    width: 600px;
    height: 342px;
    border-radius: 22px;
  }
  .card-front { left: 314px; top: 113px; background: var(--paper); }
  .card-back { left: 311px; top: 473px; background: var(--navy); }

  .wordmark {
    position: absolute;
    left: 0; right: 0;
    display: flex;
    justify-content: center;
    align-items: center;
    gap: 12px;
    font-family: "Open Sans", Arial, sans-serif;
    font-weight: 700;
    letter-spacing: -0.5px;
  }
  .wordmark-front { top: 74px; font-size: 38px; color: var(--navy); }
  .wordmark-front .mark-square { width: 30px; height: 30px; background: var(--teal); }
  .wordmark-back { top: 120px; font-size: 44px; color: var(--white); }
  .wordmark-back .mark-square { width: 36px; height: 36px; background: var(--teal); }

  .divider {
    position: absolute;
    left: 38px; top: 214px;
    width: 519px; height: 1px;
    background: var(--rule);
  }

  .person { position: absolute; left: 38px; top: 229px; }
  .person-name {
    font-family: "Roboto Condensed", Arial, sans-serif;
    font-weight: 700; font-size: 21px; color: var(--teal); line-height: 24px;
  }
  .person-role {
    font-family: "Roboto Condensed", Arial, sans-serif;
    font-weight: 500; font-size: 15px; color: var(--navy); line-height: 18px;
  }
  .person-address { font-size: 14px; color: var(--grey-text); line-height: 19px; margin-top: 1px; }

  .contacts { position: absolute; right: 40px; top: 231px; list-style: none; }
  .contacts li {
    display: flex; justify-content: flex-end; align-items: center; gap: 6px;
    font-size: 14px; color: var(--grey-text); line-height: 19px;
  }
  .contacts svg { width: 13px; height: 13px; fill: var(--teal); flex: none; }

  .tagline {
    position: absolute;
    left: 95px; right: 95px; top: 278px;
    display: flex; align-items: center; gap: 6px;
    font-style: italic; font-size: 18px; color: var(--white); white-space: nowrap;
  }
  .tagline .accent { color: var(--teal); }
  .tagline-rule { flex: 1; height: 1px; }
  .tagline-rule.left { background: linear-gradient(to right, rgba(255,255,255,0), rgba(255,255,255,0.8)); }
  .tagline-rule.right { background: linear-gradient(to left, rgba(255,255,255,0), rgba(255,255,255,0.8)); }
  .tagline-text { padding: 0 2px; }
</style>
</head>
<body>
  <section class="card card-front">
    <div class="wordmark wordmark-front">
      <span class="mark-square"></span>
      <span class="wordmark-name">Brightway Haus Inc.</span>
    </div>
    <div class="divider"></div>
    <div class="person">
      <p class="person-name">MARCUS ELLERY</p>
      <p class="person-role">CEO/FOUNDER</p>
      <p class="person-address">2146 Larkspur Way<br>Halden, Alaska 38261</p>
    </div>
    <ul class="contacts">
      <li>555 210 4837
        <svg viewBox="0 0 16 16" aria-hidden="true"><path d="M3.5 1l3 3-1.6 2.2c.9 2 2.4 3.5 4.4 4.4L11.5 9l3 3-2 2.5C6.5 14 2 9.5 1.5 3.5z"/></svg>
      </li>
      <li>555 318 2906
        <svg viewBox="0 0 16 16" aria-hidden="true"><path d="M4 0h8v16H4zM5.5 2v10h5V2zM7 13.2h2v1.3H7z" fill-rule="evenodd"/></svg>
      </li>
      <li>555 742 6150
        <svg viewBox="0 0 16 16" aria-hidden="true"><path d="M4 1h8v4H4zM1 6h14v6h-3v3H4v-3H1zM5 10v3h6v-3z" fill-rule="evenodd"/></svg>
      </li>
      <li>hello@brightway.ca
        <svg viewBox="0 0 16 16" aria-hidden="true"><path d="M1 3h14v1L8 9 1 4zM1 5.5l7 5 7-5V13H1z"/></svg>
      </li>
    </ul>
  </section>

  <section class="card card-back">
    <div class="wordmark wordmark-back">
      <span class="mark-square"></span>
      <span class="wordmark-name">Brightway Haus Inc.</span>
    </div>
    <div class="tagline">
      <span class="tagline-rule left"></span>
      <span class="tagline-text">Where <span class="accent">Shine</span> Counts</span>
      <span class="tagline-rule right"></span>
    </div>
  </section>
</body>
</html>
```